New Business Card Design Project

Need a design that will create an impact / strong impression towards our clients for our business. We are in the lighting business and we do lighting retrofits for large commercial to industrial clientele.

Target Market(s)

Lighting Industry

Industry/Entity Type

Business

Font styles to use
Other font styles liked:
• we would like to use the font on our logo, not sure what it is though..

Requirements
Must have
• Our logo.
Nice to have
• We are open to suggestions that have to do with lighting.

```html
<!DOCTYPE html>
<html lang="en">
<head>
<meta charset="utf-8">
<title>Brightline Retrofit Group – Business Cards</title>
<link href="https://fonts.googleapis.com/css2?family=Fira+Sans:wght@400;600;700&display=swap" rel="stylesheet">
<style>
  :root {
    --bg: #e4e4e6;
    --card: #ffffff;
    --green-dark: #1c5a2a;
    --green-mid: #13883f;
    --green-light: #5cb85c;
    --ink: #4a4a4a;
  }
  * { box-sizing: border-box; margin: 0; padding: 0; }
  html, body { width: 1200px; height: 800px; overflow: hidden; }
  body {
    background: var(--bg);
    font-family: "Fira Sans", sans-serif;
    position: relative;
  }
  .card {
    position: absolute;
    top: 245px;
    width: 540px;
    height: 310px;
    background: var(--card);
    box-shadow: 0 6px 18px rgba(0,0,0,0.12);
    overflow: hidden;
  }
  .card--contact { left: 40px; }
  .card--brand { left: 620px; }
  .card__band { position: absolute; left: 0; bottom: 0; width: 540px; height: 34px; }

  .brand {
    display: flex;
    align-items: center;
    gap: 10px;
    color: var(--green-mid);
    font-weight: 700;
    letter-spacing: 0.5px;
  }
  .brand__mark { background: var(--green-dark); flex: none; }
  .card--contact .brand { position: absolute; top: 44px; right: 34px; font-size: 22px; }
  .card--contact .brand__mark { width: 18px; height: 18px; }
  .card--brand .brand { position: absolute; top: 108px; left: 0; right: 0; justify-content: center; font-size: 34px; }
  .card--brand .brand__mark { width: 28px; height: 28px; }

  .person { position: absolute; top: 42px; left: 36px; }
  .person__name { color: var(--green-mid); font-weight: 600; font-size: 21px; letter-spacing: 0.5px; }
  .person__role { color: var(--ink); font-size: 13px; margin-top: 2px; }

  .contact { position: absolute; top: 116px; left: 36px; font-size: 13.5px; color: var(--ink); line-height: 1.7; list-style: none; }
  .contact__label { color: var(--green-mid); display: inline-block; width: 22px; }

  .address { position: absolute; top: 170px; left: 232px; font-size: 14px; color: var(--ink); line-height: 1.5; font-style: normal; }
</style>
</head>
<body>

<section class="card card--contact">
  <div class="brand"><span class="brand__mark"></span>Brightline Retrofit Group</div>
  <div class="person">
    <p class="person__name">JOHN DOE</p>
    <p class="person__role">Director</p>
  </div>
  <ul class="contact">
    <li><span class="contact__label">T :</span>+63 900 555 0142</li>
    <li><span class="contact__label">E :</span>john@brightline-rg.com</li>
    <li><span class="contact__label">W :</span>www.brightline-rg.com</li>
  </ul>
  <address class="address">Dummy Street<br>Dummy City, Dummy Country</address>
  <svg class="card__band" viewBox="0 0 540 34" aria-hidden="true">
    <polygon points="0,14 352,14 340,34 0,34" fill="var(--green-dark)"/>
    <polygon points="358,14 540,14 540,34 346,34" fill="var(--green-mid)"/>
  </svg>
</section>

<section class="card card--brand">
  <div class="brand"><span class="brand__mark"></span>Brightline Retrofit Group</div>
  <svg class="card__band" viewBox="0 0 540 34" aria-hidden="true">
    <polygon points="0,14 410,14 398,34 0,34" fill="var(--green-mid)"/>
    <polygon points="416,14 540,14 540,34 404,34" fill="var(--green-dark)"/>
  </svg>
</section>

</body>
</html>
```